FinTech company looking to revamp and expand client-facing interface for our financial models

Pellworth Engines currently has a very simple website that allows clients to interact with our financial models. We are looking to completely redesign the current site and add several extra pages to provide extra functionality. We want the design to have a modern, slick feel, that will work on both a desktop or a tablet. It should be straightforward for clients to move between different pages at any time, and clear from the layout how to interact with the more advanced features. We have included screenshots of existing pages in the attached design brief, as well as sketches of the functionality required by the new pages, but can't provide a direct link to the current site.
Target Market(s)
Professional investors that will be paying to access the interface
Industry/Entity Type
Finance
Number of Pages Required
4 page
Colors
Designer to choose colors to be used in the design.
Look and feel
Each slider illustrates characteristics of the customer's brand and the style your logo design should communicate.

```html
<!DOCTYPE html>
<html lang="en">
<head>
<meta charset="utf-8">
<title>Pellworth · ETF Pairs Models</title>
<link rel="stylesheet" href="https://fonts.googleapis.com/css2?family=Roboto:wght@400;500;700&family=Roboto+Condensed:wght@400;500;700&display=swap">
<style>
:root{
  --frame:#e7e7e7;
  --band:#ebebeb;
  --white:#ffffff;
  --navy:#0b3263;
  --teal:#05695f;
  --ink:#111111;
  --row-alt:#eeeeee;
  --line:#dddddd;
  --panel-head:#666666;
  --panel-body:#f0f0f0;
  --black:#141414;
}
*{box-sizing:border-box;margin:0;padding:0}
html,body{width:1200px;height:706px;overflow:hidden;background:var(--frame)}
.stage{position:absolute;left:0;top:0;width:1300px;height:765px;transform:scale(.9231);transform-origin:0 0;font-family:"Roboto",Arial,sans-serif;color:var(--ink)}
.page{position:absolute;left:15px;top:15px;width:1270px;height:735px;background:linear-gradient(180deg,var(--band) 0,var(--band) 155px,#f3f3f3 155px,#fafafa 100%)}
.abs{position:absolute}

/* top bar */
.topbar{left:15px;top:15px;width:1270px;height:60px;background:var(--white);box-shadow:0 6px 10px rgba(0,0,0,.08)}
.brand{left:60px;top:15px;height:60px;line-height:60px;font-weight:500;font-size:19px;color:var(--ink)}
.period,.nav{top:15px;height:60px;display:flex;align-items:center;justify-content:center;font-weight:700;font-size:14px;border-right:1px solid #e6e6e6}
.period.active,.nav.active{background:var(--navy);color:var(--white)}
.nav svg{margin-right:9px}

/* tabs */
.tab{display:flex;align-items:center;justify-content:center;font-weight:700;font-size:13px;color:#444;background:var(--white);box-shadow:0 -2px 6px rgba(0,0,0,.06);border-radius:3px 3px 0 0;letter-spacing:.3px}
.tab.current{background:var(--black);color:var(--white)}
.tab-arrow{background:var(--white);display:flex;align-items:center;justify-content:center}
.tab-add{background:var(--navy);display:flex;align-items:center;justify-content:center}

.export{left:1165px;top:211px;display:flex;align-items:center;gap:8px;color:var(--navy);font-weight:700;font-size:18px}

/* table */
.models{left:105px;top:250px;width:1160px;border-collapse:collapse;background:var(--white);box-shadow:0 2px 8px rgba(0,0,0,.1);font-family:"Roboto Condensed",Arial,sans-serif;table-layout:fixed}
.models th{height:70px;background:var(--teal);color:var(--white);font-family:"Roboto",Arial,sans-serif;font-weight:700;font-size:17px;text-align:left;padding-left:22px;border-left:1px solid rgba(255,255,255,.25)}
.models td{height:70px;font-size:16px;padding-left:9px;border-left:1px solid var(--line);line-height:1.25}
.models td.name{padding-left:22px}
.models tr:nth-child(even) td{background:var(--row-alt)}

/* filter overlay */
.veil{left:15px;top:170px;width:490px;height:430px;background:rgba(255,255,255,.84)}
.veil-tab{left:460px;top:260px;width:95px;height:200px;background:rgba(255,255,255,.84);border-radius:0 4px 4px 0}
.veil-head{left:460px;top:260px;width:95px;height:60px;background:rgba(225,240,238,.9);font-weight:700;font-size:17px;display:flex;align-items:center;justify-content:center}
.veil-head span{color:#b8d7d3}
.filters-tag{left:505px;top:345px;width:40px;height:80px;display:flex;align-items:center;justify-content:center}
.filters-tag span{transform:rotate(-90deg);font-weight:700;font-size:15px;letter-spacing:1px;white-space:nowrap}
.collapse{left:542px;top:372px;width:26px;height:26px;border-radius:50%;background:var(--navy);border:2px solid var(--white);box-shadow:0 0 0 1px #bbb;display:flex;align-items:center;justify-content:center}

.filters{left:75px;top:245px;width:370px;height:280px;background:var(--panel-body);box-shadow:0 2px 8px rgba(0,0,0,.2);border-radius:3px;overflow:hidden}
.filters h2{height:50px;background:var(--panel-head);color:var(--white);font-size:18px;font-weight:700;text-align:center;line-height:50px}
.frow{height:51px;border-bottom:1px solid #e0e0e0;display:flex;align-items:center;padding-left:16px;font-size:17px}
.frow .lbl{width:86px}
.frow b{margin-right:12px}
.frow .field{width:152px;height:30px;background:var(--white);border:1px solid #cfcfcf;border-radius:4px;font-size:16px;padding:4px 12px;margin-left:auto;margin-right:14px;box-shadow:inset 0 1px 2px rgba(0,0,0,.08)}
.check{display:inline-flex;align-items:center;font-weight:700}
.check.first{margin-left:24px}
.check.second{margin-left:28px}
.check i{width:17px;height:17px;border:1px solid #999;border-radius:3px;background:var(--white);margin-right:10px}
.search{position:absolute;left:108px;top:216px;width:154px;height:48px;background:var(--navy);color:var(--white);font-weight:700;font-size:15px;display:flex;align-items:center;justify-content:center;border-radius:3px;box-shadow:0 2px 4px rgba(0,0,0,.3)}
</style>
</head>
<body>
<div class="stage">
  <div class="page abs"></div>

  <header class="topbar abs"></header>
  <div class="brand abs">Pellworth</div>
  <div class="period active abs" style="left:195px;width:90px">250D</div>
  <div class="period abs" style="left:285px;width:90px">83D</div>
  <div class="period abs" style="left:375px;width:90px">42D</div>

  <div class="nav active abs" style="left:600px;width:141px">
    <svg width="24" height="22" viewBox="0 0 24 22" fill="none" stroke="#fff" stroke-width="2"><path d="M2 11 12 2l10 9"/><path d="M5 9v11h5v-6h4v6h5V9"/></svg>MODELS</div>
  <div class="nav abs" style="left:741px;width:177px">
    <svg width="24" height="24" viewBox="0 0 24 24" fill="#222"><circle cx="12" cy="12" r="3"/><circle cx="12" cy="3" r="2"/><circle cx="12" cy="21" r="2"/><circle cx="3" cy="12" r="2"/><circle cx="21" cy="12" r="2"/><circle cx="5.5" cy="5.5" r="1.7"/><circle cx="18.5" cy="5.5" r="1.7"/><circle cx="5.5" cy="18.5" r="1.7"/><circle cx="18.5" cy="18.5" r="1.7"/></svg>SENSITIVITIES</div>
  <div class="nav abs" style="left:918px;width:160px">
    <svg width="24" height="24" viewBox="0 0 24 24" fill="none" stroke="#222" stroke-width="2"><circle cx="6" cy="6" r="4"/><circle cx="18" cy="6" r="4"/><circle cx="6" cy="18" r="4"/><circle cx="18" cy="18" r="4"/></svg>PORTFOLIO</div>
  <div class="nav abs" style="left:1078px;width:152px">
    <svg width="26" height="22" viewBox="0 0 26 22" fill="none" stroke="#222" stroke-width="2"><rect x="1" y="1" width="24" height="20"/><path d="M1 6h24"/><path d="M5 17l5-6 4 3 7-6"/></svg>BACKTEST</div>

  <div class="tab abs" style="left:70px;top:135px;width:155px;height:35px">EQUITIES</div>
  <div class="tab abs" style="left:230px;top:135px;width:155px;height:35px">ETFS</div>
  <div class="tab abs" style="left:390px;top:125px;width:155px;height:45px">PAIRS</div>
  <div class="tab current abs" style="left:550px;top:115px;width:155px;height:55px">ETF PAIRS</div>
  <div class="tab abs" style="left:711px;top:125px;width:154px;height:45px">FACTORS</div>
  <div class="tab abs" style="left:870px;top:135px;width:155px;height:35px">NEW TAB TITLE #1</div>
  <div class="tab abs" style="left:1030px;top:135px;width:155px;height:35px">NEW TAB TITLE #2</div>
  <div class="tab-arrow abs" style="left:1190px;top:135px;width:40px;height:35px"><svg width="12" height="18" viewBox="0 0 12 18" fill="none" stroke="#999" stroke-width="3"><path d="M2 2l7 7-7 7"/></svg></div>
  <div class="tab-add abs" style="left:1235px;top:135px;width:40px;height:35px"><svg width="24" height="24" viewBox="0 0 24 24" fill="none" stroke="#fff" stroke-width="2"><circle cx="12" cy="12" r="10"/><path d="M12 7v10M7 12h10"/></svg></div>

  <div class="export abs"><svg width="26" height="24" viewBox="0 0 26 24" fill="none" stroke="#0b3263" stroke-width="2.4"><path d="M10 4H3v18h18v-7"/><path d="M9 16c1-6 5-9 12-9"/><path d="M17 3l5 4-5 4"/></svg>Export</div>

  <table class="models abs">
    <colgroup><col style="width:100px"><col style="width:140px"><col style="width:115px"><col style="width:85px"><col style="width:90px"><col style="width:90px"><col style="width:90px"><col style="width:90px"><col style="width:90px"><col style="width:90px"><col style="width:90px"><col style="width:90px"></colgroup>
    <thead><tr><th>Model</th><th>Sector</th><th>Date</th><th>Quality</th><th>Stat 1</th><th>Stat 2</th><th>Stat 3</th><th>Stat 4</th><th>Stat 5</th><th>Stat 6</th><th>Stat 7</th><th>Stat 8</th></tr></thead>
    <tbody>
      <tr><td class="name">Model 1</td><td>Information Technology</td><td>2019-07-03 12:15:00.000</td><td>30.2282</td><td>2.01574</td><td>23.305</td><td>-0.149368</td><td>22.3054</td><td>4.63714</td><td>0.945706</td><td>2.81949</td><td>2.60858</td></tr>
      <tr><td class="name">Model 2</td><td>Information Technology</td><td>2019-07-03 12:15:00.000</td><td>32.8694</td><td>0.87307</td><td>32.185</td><td>-0.033692</td><td>33.9911</td><td>11.5693</td><td>-0.472968</td><td>-0.830458</td><td>6.80646</td></tr>
      <tr><td class="name">Model 3</td><td>Information Technology</td><td>2019-07-03 12:15:00.000</td><td>1.66002</td><td>-0.569222</td><td>159.814</td><td>0.0252328</td><td>172.616</td><td>10.2875</td><td>-0.750396</td><td>-0.385309</td><td>4.69146</td></tr>
      <tr><td class="name">Model 4</td><td>Information Technology</td><td>2019-07-03 12:15:00.000</td><td>45.6856</td><td>0.412148</td><td>202.488</td><td>0.0084923</td><td>205.834</td><td>11.9094</td><td>-0.137913</td><td>0.449595</td><td>3.85106</td></tr>
      <tr><td class="name">Model 5</td><td>Information Technology</td><td>2019-07-03 12:15:00.000</td><td>75.7733</td><td>7.06728</td><td>188.605</td><td>0.016913</td><td>161.665</td><td>3.82241</td><td>0.981019</td><td>1.29847</td><td>3.34927</td></tr>
    </tbody>
  </table>

  <div class="veil abs"></div>
  <div class="veil-tab abs"></div>
  <div class="veil-head abs"><span>Quality</span></div>
  <div class="filters-tag abs"><span>FILTERS</span></div>
  <div class="collapse abs"><svg width="14" height="14" viewBox="0 0 14 14" fill="none" stroke="#fff" stroke-width="2"><path d="M12 7H2M6 3 2 7l4 4"/></svg></div>

  <section class="filters abs">
    <h2>Filters</h2>
    <div class="frow"><span class="lbl">Quality</span><b>Threshold:</b><span class="field">-10</span></div>
    <div class="frow"><span class="lbl"><b style="margin:0">Abs.</b> Stat</span><b>Threshold:</b><span class="field">-10</span></div>
    <div class="frow"><b style="margin-right:0">Apply</b><span class="check first"><i></i>All tabs</span><span class="check second"><i></i>Current tab</span></div>
    <div class="search">SEARCH</div>
  </section>
</div>
</body>
</html>
```